Design my site www.brieflyledger.com

So here is what I am thinking in terms of design:

https://plenvo.com

https://www.skyluxair.com

http://kalvex.com/harbor-plaza-tower/

I want the theme to be white and blue (royal blue). I attached a paint picture of what I would like the site to look like in terms of placing the text. Generally, what I like about the sites above is that they are simple, you can navigate easily and have some kind of idea of what's going on by looking at the center (picture and motto). Let's establish a clear understanding of how the functional part of the site would look like. Please see the picture attached.

I want to keep it simple: On top would be the Name 'BRIEFLY ledger", somewhere to the right on top on the page would be 'Sign in" button.

In the center would be a picture (maybe a video) with the Motto (on top of it all in capital) OBSERVE NAVIGATE DECIDE and below would be the "sign up now"

Below the picture (like on kalvex.com site) or to the left on top of the page would be "About Us', "Press" "Contact Us' buttons.

Then once the user gets to his page his got 3 tabs " Press Headlines", "Events", " Briefings".

we would keep the same format I only have on the site, but separate for every Tab.

I do not want the user to get distracted. I also want him to be able to access the page though mobile phone and be able to get automatic updates just like Zorvan Pings without having to sign in daily.

The landing page must be minimalist yet with business/corporate feel where users can navigate easily and a "what you see is what you get" approach. You want an image or video (personally I prefer the video.. it does capture the users attention instantly, as long as it is an interesting video), with your taglines in it.

Sections available to public: About Us, Contact Us, Landing Page with Signup Option

Private: Public Sections + User Account Page, Tabs for (Events, Press Headlines, Briefings)

Target Market(s)

PR/media monitoring/diplomatic community

Coding

Coded - Design and coding required

Number of Pages Required

1 page

Font styles to use
Serif
Sans Serif

Colors
0255a3
ec1f27

Requirements
Must have
• a simple landing page, that is user friendly.
Nice to have
• a video with the explanation of how to navigate the site
Should not have
• too many colors, graphs etc.

```html
<!DOCTYPE html>
<html lang="en">
<head>
<meta charset="utf-8">
<title>BRIEFLY ledger</title>
<link rel="stylesheet" href="https://fonts.googleapis.com/css2?family=Arimo:wght@400;700&family=Open+Sans:wght@400&display=swap">
<style>
  :root {
    --royal-blue: #0255a3;
    --royal-blue-dark: #0a4a8c;
    --white: #ffffff;
    --play-grey: #8c8c8c;
    --footer-top: #4b4b4b;
    --footer-bottom: #2f2f2f;
    --sky-light: #e2e6e5;
    --sky-blue: #c9dcdc;
    --glass-blue: #9fb7bd;
  }
  * { margin: 0; padding: 0; box-sizing: border-box; }
  html, body { width: 1200px; height: 657px; overflow: hidden; }
  body { font-family: "Arimo", Arial, sans-serif; position: relative; background: var(--sky-light); }

  .hero-backdrop {
    position: absolute; left: 0; top: 0; width: 1200px; height: 607px;
    background:
      linear-gradient(90deg, rgba(120,150,160,0.55) 0%, rgba(150,175,180,0.35) 30%, rgba(255,255,255,0) 46%),
      linear-gradient(180deg, var(--sky-blue) 0%, var(--sky-light) 35%, #dfe3e1 60%, #bccfd3 85%, #a9c0c6 100%);
  }

  .site-header { position: absolute; left: 0; top: 0; width: 1200px; height: 120px; }
  .brand {
    position: absolute; left: 97px; top: 50px;
    font-size: 31px; font-weight: 700; color: var(--white); letter-spacing: 0.2px;
  }
  .btn-sign-in {
    position: absolute; left: 1016px; top: 50px; width: 86px; height: 37px;
    display: flex; align-items: center; justify-content: center;
    background: linear-gradient(180deg, #1266b5 0%, var(--royal-blue-dark) 100%);
    color: var(--white); font-size: 15.5px; border-radius: 3px; text-decoration: none;
  }

  .play-button { position: absolute; left: 563px; top: 239px; width: 74px; height: 74px; }

  .motto {
    position: absolute; left: 0; top: 332px; width: 1200px; text-align: center;
    font-size: 43px; font-weight: 700; color: var(--royal-blue); letter-spacing: 0.3px;
  }
  .btn-sign-up {
    position: absolute; left: 540px; top: 408px; width: 120px; height: 37px;
    display: flex; align-items: center; justify-content: center;
    background: linear-gradient(180deg, #ffffff 0%, #ececec 100%);
    color: var(--royal-blue); font-size: 15.5px; border-radius: 3px; text-decoration: none;
  }

  .main-nav a {
    position: absolute; top: 531px; transform: translateX(-50%);
    font-size: 15.5px; font-weight: 700; color: var(--royal-blue); text-decoration: none; white-space: nowrap;
  }
  .nav-about { left: 446px; }
  .nav-press { left: 589px; }
  .nav-contact { left: 743px; }

  .site-footer {
    position: absolute; left: 0; top: 607px; width: 1200px; height: 50px;
    background: linear-gradient(180deg, var(--footer-top) 0%, var(--footer-bottom) 100%);
    font-family: "Open Sans", Arial, sans-serif; font-size: 12px; color: var(--white);
  }
  .copyright { position: absolute; left: 104px; top: 17px; }
  .footer-links a { position: absolute; top: 17px; color: var(--white); text-decoration: none; }
  .link-terms { left: 969px; }
  .link-privacy { left: 1062px; }
</style>
</head>
<body>
  <div class="hero-backdrop" role="img" aria-label="City skyline seen through the glass wall of an office tower under a pale sky"></div>

  <header class="site-header">
    <div class="brand">BRIEFLY LEDGER</div>
    <a class="btn-sign-in" href="#">SIGN IN</a>
  </header>

  <svg class="play-button" viewBox="0 0 74 74" aria-label="Play video">
    <circle cx="37" cy="37" r="37" fill="var(--play-grey)"/>
    <path d="M29 23 L29 51 L52 37 Z" fill="#ffffff" stroke="#ffffff" stroke-width="3" stroke-linejoin="round"/>
  </svg>

  <h1 class="motto">OBSERVE NAVIGATE DECIDE</h1>
  <a class="btn-sign-up" href="#">SIGN UP NOW</a>

  <nav class="main-nav">
    <a class="nav-about" href="#">ABOUT US</a>
    <a class="nav-press" href="#">PRESS</a>
    <a class="nav-contact" href="#">CONTACT US</a>
  </nav>

  <footer class="site-footer">
    <span class="copyright">Copyright © 2016 BRIEFLY ledger</span>
    <div class="footer-links">
      <a class="link-terms" href="#">Terms of Use</a>
      <a class="link-privacy" href="#">Privacy</a>
    </div>
  </footer>
</body>
</html>
```